TREVAL BUILDWORKS, LLC Webpage portfolio

I want to create a Website that allows my potential clients to browse my Skilled work via before and after photos. I want the website to enhance the work that I provide and potentially drive new business, or at least solidify my work.
I also do 3D CAD and Modeling of New Spaces and it would be nice to show some of that work from pencil design to 3D modeling, which I feel may help give me more clients.

The website needs to show a solid carpenter/company with the skills to get any project completed.

Types of Jobs - Custom Carpentry & Finishes, Kitchens, Baths, Basements, Decks, Porches, Whole House Renovation - Skilled Craftsmanship (Hardwood Flooring, Floor and Wall Tile) and much more...

Target Market(s)

Residential Home Renovation, Kitchen and Bath Renovation, Home Improvement

Industry/Entity Type

Residential Construction

Number of Pages Required

5+ page

Font styles to use
Sans Serif
Script

Requirements
Must have
• Similar to Plinvo.com, except for Treval Buildworks.
• Must be inviting.
• My Services Offered
• A way to reach me or contact me for estimates with some sort of Screening Questionare.
Nice to have
• Inviting Colors
Should not have
• Not sure at this time

```html
<!DOCTYPE html>
<html lang="en">
<head>
<meta charset="utf-8">
<title>Treval Buildworks</title>
<link rel="stylesheet" href="https://fonts.googleapis.com/css2?family=Questrial&family=Montserrat:wght@400;500&display=swap">
<style>
  :root {
    --page: #2a2a2a;
    --stripe: #1d1d1d;
    --panel: #1a1a1a;
    --text: #ececec;
    --muted: #c4c4c4;
    --field: #1f1f1f;
    --field-line: #333;
    --button: #3b3b3b;
  }
  * { box-sizing: border-box; margin: 0; padding: 0; }
  html, body { width: 720px; height: 1200px; overflow: hidden; }
  body {
    position: relative;
    background: var(--page) repeating-linear-gradient(90deg, var(--page) 0 5px, var(--stripe) 5px 7px);
    font-family: "Questrial", sans-serif;
    color: var(--text);
  }
  .abs { position: absolute; }

  /* header */
  .brand { left: 32px; top: 26px; display: flex; align-items: center; gap: 7px; font-size: 14px; color: var(--muted); }
  .brand-mark { width: 12px; height: 12px; background: var(--muted); }
  .social { display: flex; gap: 10px; align-items: center; }
  .social span { width: 9px; height: 9px; background: var(--text); border-radius: 50%; display: block; }
  .header-social { left: 486px; top: 30px; }
  .phone { left: 597px; top: 28px; font-size: 10.5px; }
  .nav { left: 489px; top: 59px; display: flex; gap: 19px; font-size: 6.5px; letter-spacing: .2px; }

  /* section headings */
  .section-title { left: 30px; font-size: 20px; line-height: 26px; font-weight: 400; letter-spacing: 1px; text-transform: uppercase; color: var(--text); z-index: 2; }
  .side-copy { left: 30px; font-size: 6.5px; line-height: 8.7px; text-transform: uppercase; color: var(--text); z-index: 2; }
  .side-copy p { margin-bottom: 8px; }
  .side-copy .lead { font-size: 10px; line-height: 13px; margin-bottom: 0; }

  /* image areas */
  .services-image { left: 82px; top: 90px; width: 608px; height: 300px;
    background:
      linear-gradient(180deg, rgba(255,255,255,0) 0 68%, rgba(225,225,222,.35) 78%, rgba(120,120,118,.2) 92%, rgba(60,60,58,.3) 100%),
      radial-gradient(ellipse 30% 40% at 84% 50%, rgba(200,200,196,.35), rgba(0,0,0,0) 100%),
      linear-gradient(90deg, #7d7d7b 0 27.6%, #6b6a68 27.6% 46%, #6f6e6b 46% 64%, #5a5855 64% 100%); }
  .work-image { left: 168px; top: 390px; width: 522px; height: 390px;
    background:
      radial-gradient(ellipse 60% 22% at 60% 58%, rgba(150,112,70,.55), rgba(0,0,0,0) 100%),
      linear-gradient(180deg, #2a2623 0%, #35302b 25%, #4b3f33 40%, #5e4a36 58%, #4a3b2e 70%, #2f2b27 85%, #262320 100%); }
  .work-detail { left: 82px; top: 450px; width: 290px; height: 133px;
    background:
      linear-gradient(160deg, rgba(0,0,0,0) 55%, rgba(60,40,28,.5) 100%),
      linear-gradient(90deg, #6a3b26 0%, #8a5238 25%, #6b4430 45%, #7a5a3e 60%, #c49a63 80%, #a27a4e 100%); }
  .work-social { left: 84px; top: 721px; }

  /* contact */
  .contact-panel { left: 82px; top: 780px; width: 608px; height: 420px; background: var(--panel); }
  .email-label { left: 168px; top: 809px; font-size: 6.5px; color: var(--muted); }
  .email { left: 168px; top: 819px; font-size: 11px; }
  .intro { left: 168px; top: 899px; font-size: 6.3px; color: var(--muted); }
  .question { left: 168px; font-family: "Montserrat", sans-serif; font-size: 9.5px; }
  .answer { left: 168px; width: 326px; height: 20px; background: var(--field); border: 1px solid var(--field-line);
    font-size: 9px; color: #3d3d3d; padding: 4px 7px; }
  .submit { left: 168px; top: 1110px; width: 82px; height: 19px; background: var(--button);
    font-family: "Montserrat", sans-serif; font-size: 9px; text-align: center; line-height: 19px; }
  .contact-social { left: 170px; top: 1179px; }
</style>
</head>
<body>
  <header>
    <div class="abs brand"><span class="brand-mark"></span>Treval Buildworks</div>
    <div class="abs social header-social"><span></span><span></span><span></span><span></span></div>
    <div class="abs phone">+1 (555) 014-2290</div>
    <nav class="abs nav"><span>MY SERVICES</span><span>BROWSE MY WORK</span><span>CONTACT ME</span></nav>
  </header>

  <section class="services">
    <div class="abs services-image" role="img" aria-label="Living room shown from pencil sketch to finished 3D render"></div>
    <h2 class="abs section-title" style="top:87px">My<br>Services</h2>
    <div class="abs side-copy" style="top:180px">
      <p>3D CAD modelling of new<br>spaces</p>
      <p>Custom<br>carpentry &amp; finishes,</p>
      <p>Kitchens,<br>baths,<br>basements,<br>decks,<br>porches,</p>
      <p><span class="lead">Whole house<br>renovation</span><br>Skilled craftsmanship<br>(hardwood flooring,<br>floor and wall tile)</p>
      <p>And much more</p>
    </div>
  </section>

  <section class="work">
    <div class="abs work-image" role="img" aria-label="Finished conference room with long wooden tables and black chairs"></div>
    <div class="abs work-detail" role="img" aria-label="Close-up of brick wall and hardwood floor finish"></div>
    <h2 class="abs section-title" style="top:447px">Browse<br>my work</h2>
    <div class="abs side-copy" style="top:539px"><p>Brose my work in<br>before and after<br>photos</p></div>
    <div class="abs social work-social"><span></span><span></span><span></span><span></span></div>
  </section>

  <section class="contact">
    <div class="abs contact-panel"></div>
    <h2 class="abs section-title" style="top:807px">Drop us<br>a line</h2>
    <div class="abs side-copy" style="top:899px"><p>Write to us<br>or,<br>respond to the<br>questionairre</p></div>
    <div class="abs side-copy" style="top:989px"><p>Your feedback is<br>very important us.<br>We'll try our utmost<br>to reply back</p></div>

    <div class="abs email-label">Email us at:</div>
    <div class="abs email">hello@trevalbuildworks.com</div>
    <div class="abs intro">Please spare a moment and answer the following questions:</div>

    <div class="abs question" style="top:929px">Lorem ipsum doler sit amet?</div>
    <div class="abs answer" style="top:948px">Your answer</div>
    <div class="abs question" style="top:989px">Lorem ipsum doler sit amet?</div>
    <div class="abs answer" style="top:1008px">Your answer</div>
    <div class="abs question" style="top:1049px">Lorem ipsum doler sit amet?</div>
    <div class="abs answer" style="top:1068px">Your answer</div>

    <div class="abs submit">SUBMIT</div>
    <div class="abs social contact-social"><span></span><span></span><span></span><span></span></div>
  </section>
</body>
</html>
```